Web design

We need the design for the logo and website for a women fashion website. No coding required. The colors used should be neutral (maybe with a light touch of color), the style should be modern, slightly luxurious, not too crowded. The target market is young professionals who love trendy clothes.
Updates

Need extra days to review

Target Market(s)

Young professionals

Industry/Entity Type

Apparel

Number of Pages Required

5+ page

Font styles to use
Sans Serif
Other font styles liked:
• Montserrat, Engravers Gothic, Benton Sans, gotham-book

Colors

Designer to choose colors to be used in the design.

```html
<!DOCTYPE html>
<html lang="en">
<head>
<meta charset="utf-8">
<title>VELA — Women's Fashion</title>
<link href="https://fonts.googleapis.com/css2?family=Montserrat:wght@300;400;500;600;700&display=swap" rel="stylesheet">
<style>
:root{
  --ink:#1d1d1d;
  --muted:#6b6b6b;
  --sale:#c8473b;
  --hero-a:#e9dfd3;
  --hero-b:#d6c6b4;
  --strip:#f4ebe6;
  --cream:#fdf8ef;
  --tan:#d7c0a5;
  --white:#ffffff;
  --line:#e6e0d8;
}
*{margin:0;padding:0;box-sizing:border-box}
html,body{width:1200px;height:4884px;overflow:hidden}
body{font-family:'Montserrat',sans-serif;color:var(--ink);background:var(--white);position:relative}
.photo{position:absolute}

/* header + hero */
.hero{position:absolute;left:0;top:0;width:1200px;height:640px;background:linear-gradient(90deg,var(--hero-a),var(--hero-b) 45%,var(--hero-a))}
.hero-models{position:absolute;left:300px;top:0;width:400px;height:640px;background:linear-gradient(180deg,#c7b29b,#8e7a64 60%,#d8cbbb)}
.nav{position:absolute;top:30px;left:60px;display:flex;gap:34px;font-size:13px;font-weight:500}
.nav .sale{color:var(--sale)}
.brand{position:absolute;top:22px;left:0;width:1200px;text-align:center;font-size:26px;font-weight:500;letter-spacing:3px;line-height:32px}
.tools{position:absolute;top:26px;right:60px;display:flex;gap:16px;align-items:center;font-size:12px}
.hero-title{position:absolute;left:712px;top:244px;font-size:44px;font-weight:300;letter-spacing:1px;line-height:1.2;text-transform:uppercase}
.hero-title strong{font-weight:600}
.hero-title .boxed{display:inline-block;background:var(--white);padding:0 14px;margin-top:6px}
.btn-dark{position:absolute;left:716px;top:372px;background:#2a2a2a;color:var(--white);font-size:12px;font-weight:600;padding:12px 28px;letter-spacing:1px}
.arrow{position:absolute;top:316px;font-size:26px;color:var(--ink)}
.dots{position:absolute;left:566px;top:604px;display:flex;gap:8px}
.dots i{width:10px;height:10px;border-radius:50%;background:var(--white);opacity:.7}
.dots i:first-child{background:var(--ink);opacity:1}

.features{position:absolute;top:640px;left:0;width:1200px;height:88px;background:var(--strip);display:flex;justify-content:space-around;align-items:center;font-size:14px;font-weight:500}
.feature{display:flex;align-items:center;gap:14px}
.feature .ico{width:40px;height:40px;border-radius:50%;background:var(--white);display:flex;align-items:center;justify-content:center}

.sec-title{position:absolute;left:0;width:1200px;text-align:center;font-size:36px;font-weight:600}
.tile-label{position:absolute;font-size:11px;font-weight:600;text-transform:uppercase;border-bottom:2px solid var(--ink);padding-bottom:3px}

.band-photo{position:absolute;left:0;top:1920px;width:1200px;height:508px;background:linear-gradient(120deg,#6f5b4c,#9a7e65 40%,#4e4a46 70%,#a59a8c)}

.popular{position:absolute;left:0;top:2428px;width:1200px;height:1012px;background:var(--cream)}
.popular h2{position:absolute;left:100px;top:70px;font-size:34px;font-weight:600}
.tabs{position:absolute;right:100px;top:82px;display:flex;gap:40px;font-size:14px;color:var(--muted)}
.tabs .on{color:var(--ink);border-bottom:2px solid var(--ink)}
.card{position:absolute;width:240px}
.card .img{height:312px}
.card .tag{position:absolute;right:8px;top:280px;background:var(--white);font-size:10px;padding:3px 8px}
.card .name{display:flex;justify-content:space-between;font-size:15px;font-weight:600;margin-top:14px}
.card .desc{font-size:13px;color:var(--muted);margin-top:6px}
.card .price{display:flex;justify-content:space-between;align-items:center;margin-top:8px;font-size:18px;font-weight:700}
.card .price s{font-size:11px;color:var(--muted);font-weight:400;margin-left:6px}
.card .sizes{font-size:10px;font-weight:500;color:var(--muted);letter-spacing:2px}

.insta-title{position:absolute;left:0;top:3520px;width:1200px;text-align:center;font-size:38px;font-weight:600;letter-spacing:4px}
.insta-sub{position:absolute;left:0;top:3580px;width:1200px;text-align:center;font-size:15px;color:var(--muted);letter-spacing:2px;text-transform:uppercase}

.newsletter{position:absolute;left:0;top:4260px;width:1200px;height:280px;background:var(--tan)}
.newsletter h3{position:absolute;left:0;top:66px;width:1200px;text-align:center;font-size:36px;font-weight:600}
.newsletter p{position:absolute;left:0;top:122px;width:1200px;text-align:center;font-size:14px;color:#5a4a3a}
.news-input{position:absolute;left:360px;top:170px;width:300px;height:46px;background:var(--white);font-size:13px;color:var(--muted);padding:15px 20px}
.news-btn{position:absolute;left:660px;top:170px;width:170px;height:46px;background:var(--ink);color:var(--white);font-size:12px;font-weight:600;text-align:center;padding-top:16px;letter-spacing:1px}

.footer-brand{position:absolute;left:100px;top:4628px;font-size:38px;font-weight:500;letter-spacing:3px;line-height:46px}
.fcol{position:absolute;top:4600px;font-size:14px;line-height:24px;color:#3a3a3a}
.fcol h4{font-size:16px;font-weight:700;letter-spacing:1px;margin-bottom:8px;color:var(--ink)}
.social{display:flex;gap:10px;margin-top:6px}
.social i{width:22px;height:22px;border-radius:50%;border:1.5px solid var(--ink)}
.copy{position:absolute;left:0;top:4842px;width:1200px;text-align:center;font-size:12px;color:var(--muted);border-top:1px solid var(--line);padding-top:14px}
</style>
</head>
<body>

<section class="hero">
  <div class="hero-models" role="img" aria-label="Two models in neutral-toned outfits posing against a beige wall"></div>
  <nav class="nav"><span>Latest Arrivals</span><span>Clothes ▾</span><span>VELA Club</span><span class="sale">On Sale</span></nav>
  <div class="brand">VELA</div>
  <div class="tools">
    <svg width="16" height="16" viewBox="0 0 16 16"><circle cx="7" cy="7" r="5" fill="none" stroke="#1d1d1d" stroke-width="1.6"/><line x1="11" y1="11" x2="15" y2="15" stroke="#1d1d1d" stroke-width="1.6"/></svg>
    <span>INR ▾</span>
    <svg width="18" height="16" viewBox="0 0 18 16"><path d="M9 15 L2 8 A4 4 0 0 1 9 3 A4 4 0 0 1 16 8 Z" fill="none" stroke="#1d1d1d" stroke-width="1.6"/></svg>
    <svg width="16" height="18" viewBox="0 0 16 18"><circle cx="8" cy="5" r="4" fill="none" stroke="#1d1d1d" stroke-width="1.6"/><path d="M1 17 A7 7 0 0 1 15 17" fill="none" stroke="#1d1d1d" stroke-width="1.6"/></svg>
    <svg width="16" height="18" viewBox="0 0 16 18"><rect x="1" y="5" width="14" height="12" fill="none" stroke="#1d1d1d" stroke-width="1.6"/><path d="M5 5 V3 A3 3 0 0 1 11 3 V5" fill="none" stroke="#1d1d1d" stroke-width="1.6"/></svg>
  </div>
  <span class="arrow" style="left:60px">‹</span>
  <span class="arrow" style="right:60px">›</span>
  <h1 class="hero-title">Mid Season <strong>Sale</strong><br><span class="boxed">Up to <strong>60% Off</strong></span></h1>
  <a class="btn-dark">SHOP NOW</a>
  <div class="dots"><i></i><i></i><i></i></div>
</section>

<section class="features">
  <div class="feature"><span class="ico"><svg width="20" height="20" viewBox="0 0 20 20"><circle cx="10" cy="10" r="8" fill="none" stroke="#1d1d1d" stroke-width="1.5"/><ellipse cx="10" cy="10" rx="3.5" ry="8" fill="none" stroke="#1d1d1d" stroke-width="1.5"/><line x1="2" y1="10" x2="18" y2="10" stroke="#1d1d1d" stroke-width="1.5"/></svg></span>Shipping Worldwide</div>
  <div class="feature"><span class="ico"><svg width="22" height="16" viewBox="0 0 22 16"><rect x="1" y="2" width="12" height="9" fill="none" stroke="#1d1d1d" stroke-width="1.5"/><path d="M13 5 H18 L21 8 V11 H13" fill="none" stroke="#1d1d1d" stroke-width="1.5"/><circle cx="5" cy="13" r="2" fill="#1d1d1d"/><circle cx="17" cy="13" r="2" fill="#1d1d1d"/></svg></span>Free Shipping On Orders Greater Than $5</div>
  <div class="feature"><span class="ico"><svg width="20" height="20" viewBox="0 0 20 20"><path d="M4 10 A6 6 0 1 0 7 4.8" fill="none" stroke="#1d1d1d" stroke-width="1.5"/><path d="M3 3 L7 5 L5 8" fill="none" stroke="#1d1d1d" stroke-width="1.5"/></svg></span>30 Days Return Policy</div>
</section>

<h2 class="sec-title" style="top:808px">Latest Collection</h2>

<div class="photo" style="left:112px;top:888px;width:312px;height:260px;background:linear-gradient(160deg,#9b7a5e,#5e4433)" role="img" aria-label="Model in a beige draped top"></div>
<span class="tile-label" style="left:112px;top:1168px">Shop Sale Tops</span>
<div class="photo" style="left:112px;top:1212px;width:312px;height:580px;background:linear-gradient(180deg,#6b4535,#8a5f48 50%,#5a3a2c)" role="img" aria-label="Model in a fitted knit dress against a brown backdrop"></div>
<span class="tile-label" style="left:112px;top:1808px">Shop All Sale</span>

<div class="photo" style="left:440px;top:888px;width:480px;height:532px;background:linear-gradient(180deg,#e3d6c6,#c4ad93 60%,#e0d2c1)" role="img" aria-label="Model in a khaki belted playsuit"></div>
<span class="tile-label" style="left:440px;top:1432px">Shop Sale Dress</span>
<div class="photo" style="left:440px;top:1480px;width:480px;height:312px;background:linear-gradient(90deg,#5a3b2e,#7c6f6a 50%,#5a3b2e)" role="img" aria-label="Model in a grey oversized blazer"></div>
<span class="tile-label" style="left:440px;top:1808px">Shop Sale Outerwear</span>

<div class="photo" style="left:940px;top:888px;width:140px;height:252px;background:linear-gradient(180deg,#f1ede8,#3a3330)" role="img" aria-label="Black shorts product shot"></div>
<span class="tile-label" style="left:940px;top:1150px">Shop Sale Bottoms</span>
<div class="photo" style="left:940px;top:1184px;width:140px;height:244px;background:linear-gradient(180deg,#d9b9a4,#e8d9cd)" role="img" aria-label="Model in light intimates"></div>
<span class="tile-label" style="left:940px;top:1440px">Shop Sale Intimates</span>
<div class="photo" style="left:940px;top:1472px;width:140px;height:308px;background:linear-gradient(180deg,#e6e2de,#d8d2cc)" role="img" aria-label="Model in a white bodysuit"></div>
<span class="tile-label" style="left:940px;top:1808px">Shop Sale Basic</span>

<div class="band-photo" role="img" aria-label="Two models in autumn jackets posing on a rocky hillside"></div>

<section class="popular">
  <h2>Popular Items</h2>
  <div class="tabs"><span class="on">All</span><span>Popular</span><span>Discount</span><span>New</span></div>

  <div class="card" style="left:100px;top:132px"><div class="img" style="background:linear-gradient(180deg,#ece8e4,#d9d3cd)" role="img" aria-label="Model in a white knit dress"></div><span class="tag">New</span><div class="name">Product Name <span>♡</span></div><div class="desc">Lorem ipsum dolor sit amet</div><div class="price"><span>$32.99<s>$45.00</s></span><span class="sizes">S M L XL</span></div></div>
  <div class="card" style="left:352px;top:132px"><div class="img" style="background:linear-gradient(180deg,#e8d0b4,#7a2a33 40%,#e2c9ad)" role="img" aria-label="Model in a burgundy knit dress"></div><div class="name">Product Name <span>♡</span></div><div class="desc">Lorem ipsum dolor sit amet</div><div class="price"><span>$32.99<s>$45.00</s></span><span class="sizes">S M L XL</span></div></div>
  <div class="card" style="left:608px;top:132px"><div class="img" style="background:linear-gradient(180deg,#e2c7a6,#6e3b2a 60%,#d9bd9c)" role="img" aria-label="Model in a brown polka dot blouse"></div><div class="name">Product Name <span>♡</span></div><div class="desc">Lorem ipsum dolor sit amet</div><div class="price"><span>$32.99<s>$45.00</s></span><span class="sizes">S M L XL</span></div></div>
  <div class="card" style="left:860px;top:132px"><div class="img" style="background:linear-gradient(180deg,#efebe7,#2d2a29 60%,#f0ece8)" role="img" aria-label="Black trousers and heels product shot"></div><span class="tag">Sale</span><div class="name">Product Name <span>♡</span></div><div class="desc">Lorem ipsum dolor sit amet</div><div class="price"><span>$32.99<s>$45.00</s></span><span class="sizes">S M L XL</span></div></div>

  <div class="card" style="left:100px;top:552px"><div class="img" style="background:linear-gradient(180deg,#8a5a48,#5b4d5a 50%,#7b4d3b)" role="img" aria-label="Model in a patterned silk dress"></div><span class="tag">New</span><div class="name">Product Name <span>♡</span></div><div class="desc">Lorem ipsum dolor sit amet</div><div class="price"><span>$32.99<s>$45.00</s></span><span class="sizes">S M L XL</span></div></div>
  <div class="card" style="left:352px;top:552px"><div class="img" style="background:linear-gradient(180deg,#e4d8c8,#f2eeea 50%,#d9ccbb)" role="img" aria-label="Model in a polka dot wrap dress"></div><div class="name">Product Name <span>♡</span></div><div class="desc">Lorem ipsum dolor sit amet</div><div class="price"><span>$32.99<s>$45.00</s></span><span class="sizes">S M L XL</span></div></div>
  <div class="card" style="left:608px;top:552px"><div class="img" style="background:linear-gradient(180deg,#d6c2aa,#f1ece6 50%,#c9b399)" role="img" aria-label="Model in a white shirt and trousers"></div><div class="name">Product Name <span>♡</span></div><div class="desc">Lorem ipsum dolor sit amet</div><div class="price"><span>$32.99<s>$45.00</s></span><span class="sizes">S M L XL</span></div></div>
  <div class="card" style="left:860px;top:552px"><div class="img" style="background:linear-gradient(180deg,#ddd2c6,#9c7a5d 55%,#d8ccbf)" role="img" aria-label="Model in a camel trench coat"></div><span class="tag">Sale</span><div class="name">Product Name <span>♡</span></div><div class="desc">Lorem ipsum dolor sit amet</div><div class="price"><span>$32.99<s>$45.00</s></span><span class="sizes">S M L XL</span></div></div>
</section>

<h2 class="insta-title">#VELA</h2>
<p class="insta-sub">Tag us @VELA for a chance to be featured on our Instagram</p>

<div class="photo" style="left:100px;top:3620px;width:240px;height:260px;background:linear-gradient(180deg,#e8dfd6,#3f8a5c 50%,#e4dad0)" role="img" aria-label="Model in a green top"></div>
<div class="photo" style="left:352px;top:3620px;width:240px;height:260px;background:linear-gradient(180deg,#c9ab8d,#a9845f)" role="img" aria-label="Model in a tan suit"></div>
<div class="photo" style="left:608px;top:3620px;width:240px;height:260px;background:linear-gradient(180deg,#d2c4b2,#5e5040 55%,#cdbda9)" role="img" aria-label="Model in an olive jumpsuit"></div>
<div class="photo" style="left:860px;top:3620px;width:240px;height:260px;background:linear-gradient(180deg,#e9d6c9,#dcc0ad)" role="img" aria-label="Model in cream lingerie"></div>
<div class="photo" style="left:100px;top:3892px;width:240px;height:268px;background:linear-gradient(180deg,#e9ebee,#cfd4da)" role="img" aria-label="Model in white activewear"></div>
<div class="photo" style="left:352px;top:3892px;width:240px;height:268px;background:linear-gradient(180deg,#c8ccd2,#e6e4e2)" role="img" aria-label="Model in a flowing white gown"></div>
<div class="photo" style="left:608px;top:3892px;width:240px;height:268px;background:linear-gradient(180deg,#eceae8,#d8d4d0)" role="img" aria-label="Model in a white shirt"></div>
<div class="photo" style="left:860px;top:3892px;width:240px;height:268px;background:linear-gradient(180deg,#e2e4e8,#6d8fb8 55%,#d8dce2)" role="img" aria-label="Model in a denim shirt"></div>

<section class="newsletter">
  <h3>Sign For Newsletter</h3>
  <p>Receive updates, the latest stuff including 10% off your first order.</p>
  <div class="news-input">Email Address</div>
  <div class="news-btn">SUBSCRIBE</div>
</section>

<div class="footer-brand">VELA</div>
<div class="fcol" style="left:448px"><h4>HELP</h4>Terms &amp; Conditions<br>Privacy Policy<br>Returns/Exchanges<br>Delivery Information<br>FAQ</div>
<div class="fcol" style="left:740px"><h4>SHOP</h4>Tops<br>Bottoms<br>Intimates<br>Dresses<br>Basic</div>
<div class="fcol" style="left:960px"><h4>CONTACT US</h4>✉ hello@vela-studio.com<h4 style="margin-top:14px">FOLLOW US</h4><div class="social"><i></i><i></i><i></i><i></i></div></div>
<div class="copy">©2021 VELA</div>

</body>
</html>
```